Product labels for new supplements business targeting high performing creative people

I need a label design for different supplements like Whey, BCAA, Melatonin etc. that I could customize for each use case separately.

The brand is called moonquell.life, and it would be the first design of the labels. We haven't sold any products yet, but the target audience is people with growth mindset, people who want to be as efficient as possible and are constantly looking to improve their lifestyle. As part of that, they are also working out, but don't know much about supplements yet. Mostly people between 20-34.

I don't have a too specific idea of the expected design, though it should be light, warm, smart and minimalist, maybe have some patterns. It should looks smart and clean (and expensive). Orange and golden might be the additional colors for white. I have attached the templates of some products that I plan to sell and also the logo of the brand.

Here's what I have used for inspiration:
Brands that I like and are somewhat similar in concept: https://www.vantrel.com/ (!!specially the way they
bring "how the product helps them" in focus, not "what the product is" & https://www.plomi.care/ &
https://www.delvora.com/sport/ & https://en.kalobrine.fr/ &
https://48sketchworks.com/profiles/marenhollowaydesign/designs/617482

Here's how different products look like: https://grenvolt.com/catalog

Target Market(s)

target audience is people with growth mindset, people who want to be as efficient as possible and are constantly looking to improve their lifestyle. As part of that, they are also working out, but don't know much about supplements yet. Mostly people between 20-34.

Industry/Entity Type

Supplements

Font styles to use
Sans Serif

Colors
FFC000
F8CF3A
FAE287
FDF2CF
FEFAEE
F0912C
F2A743
F7CA91
FBE8D2
FDF5EE
EE7325
F08F49
F5BC92
FAE3D3
FDF4ED

Requirements
Must have
• Clean, smart and minimalist design that can be applied for different products in different sizes, like Whey protein, BCAA, vitamins etc. available here: https://grenvolt.com/catalog
Nice to have
• Patterns, expensive look
Should not have
• Doodles, too many colors

```html
<!DOCTYPE html>
<html lang="en">
<head>
<meta charset="utf-8">
<title>moonquell.life — Beef Protein Chocolate label</title>
<link rel="stylesheet" href="https://fonts.googleapis.com/css2?family=Montserrat:wght@800;900&family=Poppins:wght@400;500&display=swap">
<style>
  :root {
    --page-bg: #fafbfc;
    --label-dark: #1a1110;
    --label-warm: #3e3330;
    --text-light: #f6f3f1;
    --accent-orange: #ee7325;
    --accent-deep: #d9431e;
  }
  * { box-sizing: border-box; margin: 0; padding: 0; }
  html, body {
    width: 1200px;
    height: 1000px;
    overflow: hidden;
    background: var(--page-bg);
  }
  .label {
    position: absolute;
    left: 240px;
    top: 155px;
    width: 720px;
    height: 690px;
    overflow: hidden;
    background: linear-gradient(115deg, var(--label-warm) 0%, var(--label-dark) 38%, var(--label-dark) 55%, var(--label-warm) 100%);
    color: var(--text-light);
    font-family: "Poppins", sans-serif;
  }
  .label__texture {
    position: absolute;
    inset: 0;
    background: radial-gradient(ellipse at 20% 45%, rgba(90, 70, 62, 0.35), transparent 55%);
  }
  .brand-name {
    position: absolute;
    top: 150px;
    left: 0;
    width: 720px;
    text-align: center;
    font-size: 38px;
    font-weight: 500;
    letter-spacing: 0.5px;
  }
  .product-title {
    position: absolute;
    top: 255px;
    right: 87px;
    font-family: "Montserrat", sans-serif;
    font-weight: 900;
    font-size: 64px;
    letter-spacing: 1px;
    line-height: 1;
  }
  .product-flavour {
    position: absolute;
    top: 330px;
    right: 87px;
    font-size: 40px;
    font-weight: 500;
    letter-spacing: 2px;
    line-height: 1;
  }
  .accent-chevron {
    position: absolute;
    inset: 0;
  }
  .benefits {
    position: absolute;
    top: 487px;
    left: 341px;
    font-size: 19px;
    line-height: 23px;
    letter-spacing: 0.6px;
  }
  .label__footer {
    position: absolute;
    top: 644px;
    left: 112px;
    right: 100px;
    display: flex;
    gap: 58px;
    font-size: 19px;
    letter-spacing: 0.8px;
  }
</style>
</head>
<body>
  <main class="label">
    <div class="label__texture" role="img" aria-label="Faint diagonal line pattern across the dark label"></div>

    <p class="brand-name">moonquell.life</p>

    <h1 class="product-title">BEEF PROTEIN</h1>
    <p class="product-flavour">CHOCOLATE</p>

    <svg class="accent-chevron" width="720" height="690" viewBox="0 0 720 690" aria-hidden="true">
      <defs>
        <linearGradient id="chevronFill" x1="0" y1="0" x2="1" y2="0">
          <stop offset="0" stop-color="var(--accent-orange)"/>
          <stop offset="1" stop-color="var(--accent-deep)"/>
        </linearGradient>
      </defs>
      <polygon points="251,440 604,427 304,474 301,620" fill="url(#chevronFill)"/>
    </svg>

    <p class="benefits">
      Hydrolyzed beef protein<br>
      with minimum fat content<br>
      Promotes muscle gain<br>
      and helps maintain<br>
      muscle mass*
    </p>

    <footer class="label__footer">
      <span class="label__category">DIETARY SUPPLEMENT</span>
      <span class="label__weight">Net Wt. 900g (31.75oz)</span>
    </footer>
  </main>
</body>
</html>
```